Various Designs

We need various designs for our new hand disinfectant dispensers that feature three extra-large windows that allow users to customize the appearance simply by changing the graphics.
Each dispenser has one window at the front and one on each side. The front window can have two different sizes. Please refer to attached zip file named Dispenser_Design_Templates.
The designs should be fresh and of high quality. Please don't just place a photo and spam me.
The design should also contain our logo (PVM Switzerland - is included in the template).
The design should further be professional enough for a medical and public setting. The dispensers will be used in hospitals, medical facilities, old pension homes, schools, restaurants, kitchens, public places etc.
We value creativity a lot!
It would be great if the dispenser features a slogan such as "Hand Hygiene Saves Lives". I have added a number of slogans at the end of this description.
Do not use dark colors such as brown. These colors do not stand for hygiene. You can use black but only in conjunction with a bright color.
The following files contain designs that I like:
- 01w
- velunadecor
- worldwide
- IMG_0137
Slogans:
- Hand Hygiene Saves Lives
- Did you wash your hands?
- Did you disinfect your hands?
- Protect Yourself and Your Patients
- Healthy Hands Start Here
- Hand Hygiene We Love... We Care... We Share...
- Clean hands prevent germs from spreading.
- Practice Good Hand Hygiene
- Save Lives: Clean Your Hands
- Save Lives: Disinfect Your Hands
- Washing Hands Saves Lives
- Wash Your Hands Please
- Be aware…..!!!!! Wash with care…..!!!!!
- Hand Hygiene Station
- Hand Hygiene Share your care, not your germs
- Good Hand Hygiene It's Critical Sanitize Wash Moisturize
- Disinfect (image of a hand)
- Clean (image of a hand)
- No Water? No Problem. Waterless Hand Rub. Keep it Handy.
- Wash your hands! If not for yourself, then do it for them.
- Practice good hygiene - it-s contagious!
- Be aware, wash with care!
- Filthy fingers forecast sickness and sadness.
- Hand Hygiene The power is in your hands
- Bury the germ, Wash your hands
- Sanitize your hands and support our clean hands initiative
- Sanitize your hands. Together we can make a difference.
- You are grand if you wash your hand.
- Holding hands feels better when they’re clean.
- Be wise wash hands often.
- Wash those germs away!!!
- Your Hands Can Be Dangerous. Disinfect them to keep germs away.
- Ten out of ten patients prefer care from clean hands.
- Safety first, disinfect and protect
- It’s universal- handwashing every patient every time!
- Infection control is in your hands.
- Make your intention prevention. Wash your hands

```html
<!DOCTYPE html>
<html lang="en">
<head>
<meta charset="utf-8">
<title>PVM Switzerland – Dispenser Window Design</title>
<link rel="stylesheet" href="https://fonts.googleapis.com/css2?family=Righteous&display=swap">
<style>
  :root {
    --page: #ffffff;
    --wash-light: #f3f6fb;
    --wash-mid: #e3e9f3;
    --water-top: #bcdcef;
    --water-mid: #8cc6e6;
    --water-deep: #6fb3dd;
    --water-green: #9fd3c4;
    --cut-line: #d8262f;
    --safe-line: #7dbb4a;
    --slogan-fill: #b9e2fa;
    --slogan-edge: #3d95d3;
    --brand: #2a5ca6;
  }
  * { margin: 0; padding: 0; box-sizing: border-box; }
  html, body {
    width: 1200px;
    height: 1000px;
    overflow: hidden;
    background: var(--page);
  }
  .canvas {
    position: relative;
    width: 1200px;
    height: 1000px;
    overflow: hidden;
    font-family: "Righteous", sans-serif;
  }
  .artwork {
    position: absolute;
    inset: 0;
  }
  .slogan {
    position: absolute;
    left: 292px;
    width: 600px;
    top: 156px;
    text-align: center;
    font-size: 38px;
    line-height: 52px;
    letter-spacing: 0.5px;
    color: var(--slogan-fill);
    -webkit-text-stroke: 1.6px var(--slogan-edge);
    paint-order: stroke fill;
  }
  .brand {
    position: absolute;
    left: 414px;
    top: 812px;
    display: flex;
    align-items: baseline;
    gap: 26px;
    color: var(--brand);
  }
  .brand-name {
    font-size: 78px;
    line-height: 1;
    letter-spacing: 8px;
  }
  .brand-country {
    font-size: 22px;
    line-height: 1;
  }
</style>
</head>
<body>
<main class="canvas">
  <svg class="artwork" width="1200" height="1000" viewBox="0 0 1200 1000" aria-hidden="false">
    <defs>
      <linearGradient id="wash" x1="0" y1="0" x2="1" y2="1">
        <stop offset="0" stop-color="var(--wash-mid)"/>
        <stop offset="0.4" stop-color="var(--wash-light)"/>
        <stop offset="1" stop-color="var(--wash-mid)"/>
      </linearGradient>
      <linearGradient id="water" x1="0" y1="0" x2="0" y2="1">
        <stop offset="0" stop-color="var(--water-top)"/>
        <stop offset="0.45" stop-color="var(--water-mid)"/>
        <stop offset="1" stop-color="var(--water-deep)"/>
      </linearGradient>
      <linearGradient id="water-tint" x1="0" y1="0" x2="1" y2="0">
        <stop offset="0.6" stop-color="var(--water-green)" stop-opacity="0"/>
        <stop offset="1" stop-color="var(--water-green)" stop-opacity="0.6"/>
      </linearGradient>
    </defs>

    <g class="background">
      <rect class="watercolour-wash" x="212" y="0" width="776" height="1000" fill="url(#wash)"
            role="img" aria-label="Soft pale blue watercolour texture"/>
      <g class="water-band" role="img" aria-label="Watercolour water surface in light blue">
        <polygon points="212,742 988,832 988,1000 212,1000" fill="url(#water)"/>
        <polygon points="212,742 988,832 988,1000 212,1000" fill="url(#water-tint)"/>
      </g>
    </g>

    <g class="trim-mask" fill="var(--page)">
      <polygon points="0,0 212,0 310,1000 0,1000"/>
      <polygon points="988,0 1200,0 1200,1000 890,1000"/>
    </g>

    <polygon class="cut-line" points="212,0 988,0 890,1000 310,1000"
             fill="none" stroke="var(--cut-line)" stroke-width="2"/>

    <path class="safe-area"
          d="M330,48 Q592,5 868,50 Q926,70 922,130 L852,880 Q846,918 800,930 Q592,985 400,930 Q352,918 346,880 L276,130 Q274,70 330,48 Z"
          fill="none" stroke="var(--safe-line)" stroke-width="2.4"/>

    <g class="mount-holes" fill="none" stroke="var(--cut-line)" stroke-width="2">
      <circle cx="265" cy="38" r="10"/>
      <circle cx="932" cy="38" r="10"/>
      <circle cx="349" cy="948" r="10"/>
      <circle cx="849" cy="948" r="10"/>
    </g>
  </svg>

  <h1 class="slogan">Be<br>Hygiene Serene.<br>Keep Your Hands Clean.</h1>

  <div class="brand">
    <span class="brand-name">PVM</span>
    <span class="brand-country">Switzerland</span>
  </div>
</main>
</body>
</html>
```